Velorin Wine Label For Canopy Haven

Lantern Brook Winery is in need of a wine label for new wine being release. This wine will be used as a fundraiser for Canopy Haven, a chimpanzee santuary in Georgia. The label should reflect a high-end, classy image and the label should suggest the chimp philanthropy without specifically naming the organization (for legal purposes). The label can be a little whimsical without being too cartoonish or child like. This wine will be sold for $30 so it should project a sense of elegance too.
Updates

holiday season makes it difficult to get feedback necessary for approval. just need a few more days...

Industry/Entity Type

Winery

Font styles to use
Sans Serif

Requirements
Must have
• Label should show common design appearance as other labels downloaded.
• Label should be a dark (emerald) green color. Label should have wine name "Velorin" in center. Label should include an image or silhouette of a chimp on it
Should not have
• no cartoonish images;

```html
<!DOCTYPE html>
<html lang="en">
<head>
<meta charset="utf-8">
<title>Velorin — Lantern Brook Winery label</title>
<link rel="stylesheet" href="https://fonts.googleapis.com/css2?family=Cinzel:wght@400;500&display=swap">
<style>
  :root {
    --backdrop: #5ed6b4;
    --label-green: #2d6c55;
    --label-green-deep: #235a46;
    --ink-light: #e2ebe5;
    --art-light: #cfd6d2;
    --art-dark: #2b302e;
  }
  html, body {
    margin: 0;
    padding: 0;
    width: 1200px;
    height: 1200px;
    overflow: hidden;
    background: var(--backdrop);
  }
  .label-canvas {
    display: block;
    width: 1200px;
    height: 1200px;
  }
  .label-band { fill: var(--label-green); }
  .band-frame, .diamond-rule {
    fill: none;
    stroke: var(--ink-light);
  }
  .band-frame { stroke-width: 2; }
  .diamond-rule.outer { stroke-width: 5; }
  .diamond-rule.inner { stroke-width: 2; }
  .diamond-fill { fill: var(--label-green-deep); }
  .wine-name {
    font-family: "Cinzel", serif;
    font-weight: 400;
    font-size: 96px;
    letter-spacing: 2px;
    fill: var(--ink-light);
  }
  .winery-name {
    font-family: "Cinzel", serif;
    font-weight: 500;
    fill: var(--ink-light);
  }
  .winery-name.top { font-size: 40px; letter-spacing: 3px; }
  .winery-name.bottom { font-size: 24px; letter-spacing: 4px; }
  .side-note {
    font-family: "Cinzel", serif;
    font-size: 18px;
    letter-spacing: 1px;
    fill: var(--ink-light);
  }
</style>
</head>
<body>
<svg class="label-canvas" viewBox="0 0 1200 1200" xmlns="http://www.w3.org/2000/svg">
  <defs>
    <radialGradient id="portraitTone" cx="45%" cy="45%" r="60%">
      <stop offset="0%" stop-color="var(--art-light)"/>
      <stop offset="55%" stop-color="#7d8581"/>
      <stop offset="100%" stop-color="var(--art-dark)"/>
    </radialGradient>
    <linearGradient id="emblemTone" x1="0" y1="0" x2="1" y2="1">
      <stop offset="0%" stop-color="var(--ink-light)"/>
      <stop offset="100%" stop-color="#b9c9c0"/>
    </linearGradient>
  </defs>

  <!-- label band -->
  <g class="label">
    <rect class="label-band" x="160" y="300" width="880" height="600"/>
    <rect class="band-frame" x="176" y="316" width="848" height="568"/>

    <!-- central diamond -->
    <polygon class="diamond-fill" points="600,150 940,600 600,1050 260,600"/>
    <polygon class="diamond-rule outer" points="600,150 940,600 600,1050 260,600"/>
    <polygon class="diamond-rule inner" points="600,178 919,600 600,1022 281,600"/>

    <!-- estate emblem -->
    <rect x="565" y="295" width="70" height="70" transform="rotate(45 600 330)"
          fill="url(#emblemTone)" role="img"
          aria-label="Small estate emblem with sun, vines, hills and grapes"/>

    <!-- chimp portrait -->
    <ellipse cx="610" cy="575" rx="175" ry="155" fill="url(#portraitTone)"
             role="img" aria-label="Engraved-style side profile portrait of a chimpanzee"/>

    <!-- type -->
    <text class="wine-name" x="600" y="795" text-anchor="middle">VELORIN</text>
    <text class="winery-name top" x="600" y="852" text-anchor="middle">LANTERN</text>
    <text class="winery-name bottom" x="600" y="888" text-anchor="middle">· BROOK ·</text>

    <text class="side-note" transform="translate(214 600) rotate(-90)" text-anchor="middle">13% ALC/VOL</text>
    <text class="side-note" transform="translate(986 600) rotate(90)" text-anchor="middle">750 ML</text>
  </g>
</svg>
</body>
</html>
```